Insurance Agency website design for Brellow Cover Insurance, LP

Build a website for Brellow Cover Insurance, LP which sells Homeowners, Auto, Renters, Condo, Flood, Disability, Life, Umbrella, and health insurance. We need the coolest insurance agency website out there to get quotes, contact us, or get additional information. Please list the following insurance companies we work with: Varnix, Ostle, Meridale Mutual, Quillor, Dunmarrow, KGZ, and Pellwick.

Make a design similar to https://www.fernagentry.com/

Selling personal insurance policies

```html
<!DOCTYPE html>
<html lang="en">
<head>
<meta charset="utf-8">
<title>Brellow Cover Insurance, LP</title>
<link href="https://fonts.googleapis.com/css2?family=Lexend:wght@400;500;600;700&family=Mulish:wght@400;600;700;800&display=swap" rel="stylesheet">
<style>
:root{
  --navy:#133f8c;
  --blue:#1a74c8;
  --sky:#dbe9f7;
  --green:#7bb342;
  --green-dark:#6aa033;
  --ink:#2b2f38;
  --muted:#555b66;
  --line:#dfe4ec;
  --soft:#f3f5f9;
  --white:#ffffff;
}
*{box-sizing:border-box;margin:0;padding:0}
html,body{width:1200px;height:4332px;overflow:hidden;background:var(--white)}
body{position:relative;font-family:"Mulish",sans-serif;color:var(--ink)}
.abs{position:absolute}
h1,h2,h3,.head{font-family:"Lexend",sans-serif}
.btn{position:absolute;display:flex;align-items:center;justify-content:center;gap:8px;border-radius:30px;color:var(--white);font-family:"Lexend",sans-serif;font-weight:600;font-size:13px;letter-spacing:.4px;text-transform:uppercase}
.btn-green{background:var(--green)}
.btn-navy{background:var(--navy)}
.eyebrow{font-family:"Lexend",sans-serif;font-size:15px;letter-spacing:2px;text-transform:uppercase;color:var(--green)}
.underline{display:inline-block;position:relative}
.underline::after{content:"";position:absolute;left:4%;right:0;bottom:-8px;height:3px;border-radius:3px;background:var(--blue);transform:rotate(-1deg)}

/* hero */
.hero{left:0;top:0;width:1200px;height:726px;background:linear-gradient(180deg,#c9dcf2 0%,#e6eff9 55%,#cfe2f4 100%)}
.nav{left:74px;top:17px;width:1064px;height:92px;background:var(--white);border-radius:6px;box-shadow:0 4px 18px rgba(19,63,140,.08)}
.nav-link{position:absolute;top:36px;font-family:"Lexend",sans-serif;font-size:13px;font-weight:600;color:var(--ink)}
.nav-link.active::after{content:"";position:absolute;left:-4px;right:-4px;top:40px;height:3px;background:var(--blue)}
.brand{position:absolute;display:flex;align-items:center;gap:10px}
.brand-dot{width:34px;height:34px;border-radius:50%;border:3px solid var(--blue)}
.brand-name{font-family:"Lexend",sans-serif;font-weight:600;color:var(--navy);font-size:16px;line-height:1.1;letter-spacing:.3px;text-transform:uppercase}
.nav-phone{position:absolute;left:703px;top:34px;display:flex;align-items:center;gap:8px;font-family:"Lexend",sans-serif;font-weight:600;font-size:16px;color:var(--ink)}
.hero-photo{border-radius:0}
.hero-title{left:0;width:1200px;top:186px;text-align:center;font-size:46px;font-weight:600;color:var(--navy)}
.hero-title .mark{display:inline-block;background:var(--blue);color:var(--white);padding:0 14px;border-radius:4px;line-height:56px}
.hero-text{left:266px;width:668px;top:259px;text-align:center;font-size:15px;line-height:23px;color:var(--ink)}

/* partners */
.partners{left:0;top:726px;width:1200px;height:106px;border-bottom:1px solid var(--line);display:flex;align-items:center;justify-content:space-around;padding:0 90px}
.partner{font-family:"Lexend",sans-serif;font-weight:600;font-size:26px;color:#2a2d35;letter-spacing:2px}

/* about */
.about-photo{left:0;top:882px;width:546px;height:492px;border-radius:0 50% 50% 0/0 50% 50% 0;background:linear-gradient(135deg,#b7c9d8,#e2b35c 55%,#6f8a58)}
.about-title{left:595px;top:922px;font-size:37px;font-weight:600;color:var(--navy)}
.about-lead{left:594px;top:994px;width:540px;font-size:16px;line-height:23px;color:var(--ink);font-weight:600}
.about-body{left:597px;top:1083px;width:540px;border-left:2px solid var(--green);padding-left:16px;font-size:16px;line-height:23px;color:var(--muted)}
.about-body p+p{margin-top:14px}

/* contact */
.contact{left:0;top:1442px;width:1200px;height:541px;background:var(--soft)}
.contact-title{left:114px;top:1555px;font-size:40px;font-weight:600;color:var(--navy)}
.contact-text{left:114px;top:1632px;width:470px;font-size:14.5px;line-height:21.5px;color:var(--muted)}
.contact-text p+p{margin-top:20px}
.form-box{left:630px;top:1492px;width:459px;height:417px;background:var(--green);border-radius:34px 0 34px 0}
.field{position:absolute;left:50px;width:362px;height:44px;background:var(--white);border-radius:3px;display:flex;align-items:center;gap:10px;padding-left:20px;font-size:13px;color:#555}
.field svg{flex:none}

/* coverage */
.coverage{left:0;top:1983px;width:1200px;height:690px}
.cov-title{left:0;width:1200px;top:2093px;text-align:center;color:var(--white);font-size:31px;font-weight:500;line-height:43px}
.cov-sub{left:0;width:1200px;top:2194px;text-align:center;color:var(--white);font-family:"Lexend",sans-serif;font-size:17px}
.card{position:absolute;width:151px;height:126px;background:var(--white);border-radius:4px;text-align:center}
.card .box{position:absolute;left:10px;top:10px;width:18px;height:18px;border:1px solid #cfd6e2;border-radius:2px;background:#eef2f8}
.card svg{position:absolute;left:50%;top:30px;transform:translateX(-50%)}
.card span{position:absolute;left:0;right:0;bottom:16px;font-family:"Lexend",sans-serif;font-size:14px;font-weight:600;color:var(--navy)}

/* agent */
.agent-card{left:101px;top:2751px;width:988px;height:514px;background:var(--white);border:1px solid #bdd3ec;border-radius:4px}
.agent-photo{left:153px;top:2789px;width:402px;height:416px;border-radius:22px 22px 0 22px;background:linear-gradient(160deg,#2c86d4,#0f5fae)}
.agent-title{left:640px;top:2805px;font-size:34px;font-weight:600;line-height:34px;color:var(--navy)}
.agent-note{left:640px;top:2900px;width:400px;font-size:13.5px;line-height:20px;color:var(--blue)}
.label{font-family:"Lexend",sans-serif;font-size:14px;color:var(--ink)}
.input{position:absolute;left:643px;width:386px;height:47px;border:2px solid #c6d6ea;border-radius:3px;display:flex;align-items:center;gap:10px;padding-left:18px;font-size:13px;color:#555}

/* testimonials */
.t-title{left:0;width:1200px;top:3363px;text-align:center;font-size:31px;font-weight:600;color:var(--navy)}
.t-side{top:3535px;width:140px;height:140px;background:var(--white);border:1px solid var(--line);border-radius:8px;font-size:11px;line-height:15px;color:var(--muted);padding:18px 16px;overflow:hidden}
.t-card{left:311px;top:3461px;width:588px;height:260px;background:var(--white);border:1px solid #c8d6ea;border-radius:10px;box-shadow:0 6px 24px rgba(19,63,140,.08);text-align:center}
.avatar{position:absolute;border-radius:50%;background:linear-gradient(135deg,#c9a58a,#6b5448);border:3px solid var(--white);box-shadow:0 2px 6px rgba(0,0,0,.15)}

/* cta */
.cta{left:79px;top:3822px;width:1069px;height:143px;background:var(--green);border-radius:46px 46px 0 70px}
.cta-title{position:absolute;left:152px;top:44px;font-family:"Lexend",sans-serif;font-size:25px;font-weight:600;color:var(--white)}
.cta-sub{position:absolute;left:152px;top:87px;font-size:15px;color:var(--white)}
.cta-btn{position:absolute;left:783px;top:47px;width:209px;height:52px;background:var(--white);border-radius:26px;display:flex;align-items:center;justify-content:center;gap:6px;font-family:"Lexend",sans-serif;font-weight:600;font-size:17px;color:var(--blue)}

/* footer */
.f-col h4{font-family:"Lexend",sans-serif;font-size:14px;font-weight:600;color:var(--ink);padding-bottom:10px;border-bottom:1px solid var(--line);position:relative;width:148px;text-transform:uppercase}
.f-col h4::after{content:"";position:absolute;left:0;bottom:-1px;width:26px;height:3px;background:var(--green)}
.f-col li{list-style:none;font-size:13px;color:var(--muted);margin-top:13px}
.f-contact{display:flex;gap:14px;font-size:13px;line-height:20px;color:var(--muted);margin-top:18px}
.social{width:24px;height:24px;border-radius:50%;background:var(--blue)}
.bottom{left:0;top:4263px;width:1200px;border-top:1px solid var(--line);height:69px;font-size:11px;color:var(--muted)}
</style>
</head>
<body>

<!-- HERO -->
<section class="abs hero">
  <div class="abs hero-photo" role="img" aria-label="Smiling man in denim shirt holding a laptop" style="left:50px;top:300px;width:362px;height:426px;background:linear-gradient(180deg,rgba(47,100,170,.0),rgba(47,100,170,.45));border-radius:180px 180px 0 0"></div>
  <div class="abs hero-photo" role="img" aria-label="Smiling woman in white shirt looking at her phone" style="left:857px;top:286px;width:303px;height:440px;background:linear-gradient(180deg,rgba(196,170,150,0),rgba(196,170,150,.5));border-radius:150px 150px 0 0"></div>

  <nav class="abs nav">
    <a class="nav-link active" style="left:36px">GET INSURANCE ⌄</a>
    <a class="nav-link" style="left:240px">PERSONAL ⌄</a>
    <a class="nav-link" style="left:320px"></a>
    <a class="nav-link" style="left:320px">WHY US</a>
    <div class="brand" style="left:434px;top:24px">
      <span class="brand-dot"></span>
      <span class="brand-name">Brellow Cover<br>Insurance, LP</span>
    </div>
    <div class="nav-phone">
      <svg width="18" height="18" viewBox="0 0 24 24"><path fill="#7bb342" d="M6.6 10.8a15.1 15.1 0 0 0 6.6 6.6l2.2-2.2c.3-.3.7-.4 1-.2 1.1.4 2.3.6 3.6.6.6 0 1 .4 1 1V20c0 .6-.4 1-1 1A17 17 0 0 1 3 4c0-.6.4-1 1-1h3.5c.6 0 1 .4 1 1 0 1.3.2 2.5.6 3.6.1.3 0 .7-.2 1z"/></svg>
      (555) 218-0734
    </div>
    <div class="btn btn-green" style="left:889px;top:28px;width:142px;height:40px;font-size:12px">Get a Quote ›</div>
  </nav>

  <div class="abs eyebrow" style="left:0;width:1200px;top:156px;text-align:center;color:var(--blue);font-size:17px">Brellow Cover Insurance LP</div>
  <h1 class="abs hero-title">Protecting What <span class="mark">Matters Most</span></h1>
  <p class="abs hero-text">At Brellow Cover Insurance, we understand that your peace of mind is invaluable. Our mission is to protect what matters most to you—your home, your vehicle, your health, and your loved ones. With our comprehensive range of insurance solutions, we are dedicated to safeguarding your assets and providing you with the security you deserve.</p>
  <p class="abs" style="left:0;width:1200px;top:371px;text-align:center;font-size:16px;font-weight:600">For inquiries, please contact us at</p>
  <div class="btn btn-green" style="left:469px;top:417px;width:299px;height:48px;font-size:16px;text-transform:none;font-weight:500">
    <svg width="18" height="18" viewBox="0 0 24 24"><path fill="#fff" d="M6.6 10.8a15.1 15.1 0 0 0 6.6 6.6l2.2-2.2c.3-.3.7-.4 1-.2 1.1.4 2.3.6 3.6.6.6 0 1 .4 1 1V20c0 .6-.4 1-1 1A17 17 0 0 1 3 4c0-.6.4-1 1-1h3.5c.6 0 1 .4 1 1 0 1.3.2 2.5.6 3.6.1.3 0 .7-.2 1z"/></svg>
    Call Us (555) 218-0734</div>
  <div class="btn btn-navy" style="left:469px;top:482px;width:299px;height:48px;font-size:15px;text-transform:none;font-weight:500">
    <svg width="18" height="14" viewBox="0 0 24 18"><rect width="24" height="18" rx="2" fill="#fff"/><path d="M2 2l10 8 10-8" stroke="#133f8c" stroke-width="2" fill="none"/></svg>
    info@brellowcover.com</div>
</section>

<!-- PARTNERS -->
<section class="abs partners" aria-label="Insurance companies we work with">
  <span class="partner">VARNIX</span>
  <span class="partner">OSTLE</span>
  <span class="partner" style="letter-spacing:0">Meridale Mutual</span>
  <span class="partner" style="letter-spacing:0">Quillor</span>
  <span class="partner">KGZ</span>
</section>

<!-- ABOUT -->
<div class="abs about-photo" role="img" aria-label="Happy family playing outdoors, father carrying daughter on his shoulders"></div>
<div class="abs eyebrow" style="left:595px;top:903px">Who we are</div>
<h2 class="abs about-title"><span class="underline">Brellow Cover</span>, LP</h2>
<p class="abs about-lead">Brellow Cover Insurance is a full-service, independent insurance agency with over three decades of experience in delivering comprehensive insurance solutions to individuals.</p>
<div class="abs about-body">
  <p>We proudly offer a diverse portfolio of products from more than 20 of the most reputable and financially secure companies in the industry. Our dedicated team of over 50 skilled professionals is committed to customizing these products and services to meet the unique needs of each client.</p>
  <p>At Brellow Cover Insurance, our experts are focused on addressing the individual needs of our clients, ensuring exceptional service and support at every step</p>
</div>
<div class="btn btn-green" style="left:586px;top:1314px;width:174px;height:47px">Get a Quote ›</div>

<!-- CONTACT -->
<section class="abs contact"></section>
<div class="abs eyebrow" style="left:114px;top:1534px">Contact us</div>
<h2 class="abs contact-title"><span class="underline">Get a Quote</span></h2>
<div class="abs contact-text">
  <p>We believe that securing your home is one of the most important decisions you can make. Obtaining a comprehensive insurance quote is essential to understanding your coverage options and ensuring that your property is adequately protected against unforeseen events.</p>
  <p>Our team of experienced professionals is here to guide you through the process, helping you find the right policy that meets your specific needs and budget. Don't leave your home's safety to chance—get a quote today and take the first step towards peace of mind.</p>
</div>
<form class="abs form-box">
  <div class="field" style="top:40px"><svg width="14" height="14" viewBox="0 0 24 24"><circle cx="12" cy="7" r="5" fill="#999"/><path d="M2 24c0-6 4-9 10-9s10 3 10 9z" fill="#999"/></svg>Name</div>
  <div class="field" style="top:92px"><svg width="14" height="11" viewBox="0 0 24 18"><rect width="24" height="18" rx="2" fill="#999"/><path d="M2 2l10 8 10-8" stroke="#fff" stroke-width="2" fill="none"/></svg>Email address</div>
  <div class="field" style="top:145px"><svg width="14" height="14" viewBox="0 0 24 24"><path fill="#999" d="M6.6 10.8a15.1 15.1 0 0 0 6.6 6.6l2.2-2.2c.3-.3.7-.4 1-.2 1.1.4 2.3.6 3.6.6.6 0 1 .4 1 1V20c0 .6-.4 1-1 1A17 17 0 0 1 3 4c0-.6.4-1 1-1h3.5c.6 0 1 .4 1 1 0 1.3.2 2.5.6 3.6.1.3 0 .7-.2 1z"/></svg>Phone</div>
  <div class="field" style="top:197px"><svg width="12" height="15" viewBox="0 0 20 26"><path fill="#999" d="M10 0a10 10 0 0 1 10 10c0 7-10 16-10 16S0 17 0 10A10 10 0 0 1 10 0z"/><circle cx="10" cy="10" r="3.5" fill="#fff"/></svg>Zip Code</div>
  <div class="field" style="top:252px;height:84px;align-items:flex-start;padding-top:14px"><svg width="14" height="13" viewBox="0 0 24 22"><path fill="#999" d="M12 0C5 0 0 4 0 9c0 3 2 5 4 7l-1 6 6-4c1 0 2 .2 3 .2 7 0 12-4 12-9S19 0 12 0z"/></svg>Message</div>
  <div class="btn btn-navy" style="left:50px;top:343px;width:190px;height:43px">Send Message ›</div>
</form>

<!-- COVERAGE -->
<svg class="abs" style="left:0;top:1950px" width="1200" height="740" viewBox="0 0 1200 740" aria-hidden="true">
  <path d="M0 113 C250 40 650 30 1200 38 L1200 50 C650 45 260 60 0 140 Z" fill="#7bb342"/>
  <path d="M0 140 C260 60 650 45 1200 50 L1200 640 C1000 660 820 720 600 722 C350 724 140 680 0 655 Z" fill="#133f8c"/>
  <path d="M1200 640 C1000 660 820 720 600 722 C820 712 1000 680 1200 665 Z" fill="#7bb342"/>
  <path d="M689 0 C690 30 660 30 640 32 C615 35 610 40 610 60 L610 100" stroke="#1a74c8" stroke-width="2" stroke-dasharray="5 5" fill="none"/>
</svg>
<h2 class="abs cov-title">Now more Specifically, what type of<br>Personal Protection are you <span class="underline">looking for?</span></h2>
<p class="abs cov-sub">Select up to three coverages</p>

<div class="card" style="left:249px;top:2246px"><i class="box"></i>
  <svg width="64" height="40" viewBox="0 0 64 40" fill="none" stroke="#1a74c8" stroke-width="2"><path d="M4 28V20l6-2 8-8h22l10 8 10 2v8z"/><circle cx="16" cy="30" r="5" fill="#fff"/><circle cx="48" cy="30" r="5" fill="#fff"/><path d="M20 18h26"/></svg>
  <span>Auto</span></div>
<div class="card" style="left:434px;top:2246px"><i class="box"></i>
  <svg width="50" height="44" viewBox="0 0 50 44" fill="none" stroke="#1a74c8" stroke-width="2"><path d="M4 20L25 4l21 16"/><path d="M9 17v24h32V17"/><rect x="20" y="26" width="10" height="15"/><rect x="12" y="22" width="6" height="6"/><rect x="32" y="22" width="6" height="6"/></svg>
  <span>Home</span></div>
<div class="card" style="left:619px;top:2246px"><i class="box"></i>
  <svg width="50" height="44" viewBox="0 0 50 44" fill="none" stroke="#1a74c8" stroke-width="2"><circle cx="32" cy="12" r="9"/><circle cx="34" cy="10" r="2.5"/><path d="M25 18L8 35l3 3 3-3 3 3 3-3-3-3 6-6"/></svg>
  <span>Renters</span></div>
<div class="card" style="left:804px;top:2246px"><i class="box"></i>
  <svg width="50" height="46" viewBox="0 0 50 46" fill="none" stroke="#1a74c8" stroke-width="2"><rect x="6" y="6" width="24" height="38"/><rect x="30" y="16" width="14" height="28"/><path d="M11 12h4M20 12h4M11 19h4M20 19h4M11 26h4M20 26h4M11 33h4M20 33h4M35 23h4M35 30h4M35 37h4"/></svg>
  <span>Condo</span></div>

<div class="card" style="left:249px;top:2396px"><i class="box"></i>
  <svg width="50" height="44" viewBox="0 0 50 44" fill="none" stroke="#1a74c8" stroke-width="2"><path d="M5 16a20 12 0 0 1 40 0z"/><path d="M25 4v12"/><circle cx="13" cy="26" r="4"/><circle cx="25" cy="26" r="4"/><circle cx="37" cy="26" r="4"/><path d="M6 40c0-5 3-7 7-7s7 2 7 7M18 40c0-5 3-7 7-7s7 2 7 7M30 40c0-5 3-7 7-7s7 2 7 7"/></svg>
  <span>Umbrella</span></div>
<div class="card" style="left:434px;top:2396px"><i class="box"></i>
  <svg width="60" height="44" viewBox="0 0 60 44" fill="none" stroke="#1a74c8" stroke-width="2"><path d="M4 14L56 6v8H4z"/><rect x="6" y="14" width="48" height="24"/><rect x="12" y="20" width="10" height="18"/><rect x="28" y="20" width="20" height="10"/></svg>
  <span>Mobile Home</span></div>
<div class="card" style="left:619px;top:2396px"><i class="box"></i>
  <svg width="64" height="44" viewBox="0 0 64 44" fill="none" stroke="#1a74c8" stroke-width="2"><path d="M4 34V8h40l8 10h8v16z"/><rect x="10" y="14" width="10" height="8"/><rect x="26" y="14" width="12" height="20"/><circle cx="14" cy="36" r="5" fill="#fff"/><circle cx="50" cy="36" r="5" fill="#fff"/></svg>
  <span>Motor Home</span></div>
<div class="card" style="left:804px;top:2396px"><i class="box"></i>
  <svg width="64" height="44" viewBox="0 0 64 44" fill="none" stroke="#1a74c8" stroke-width="2"><circle cx="14" cy="30" r="9"/><circle cx="50" cy="30" r="9"/><path d="M14 30l10-12h16l10 12M28 18l4-8h8M22 24h20"/></svg>
  <span>ATV</span></div>

<div class="btn btn-green" style="left:511px;top:2555px;width:171px;height:47px">Show More ›</div>

<!-- AGENT -->
<div class="abs agent-card"></div>
<div class="abs agent-photo" role="img" aria-label="Smiling woman with glasses in a light blue sweater pointing to the form"></div>
<svg class="abs" style="left:555px;top:3150px" width="110" height="80" viewBox="0 0 110 80" aria-hidden="true"><path d="M20 10c-10 20 10 50 40 55 20 3 35-5 45-15" stroke="#1a74c8" stroke-width="1.5" stroke-dasharray="3 4" fill="none"/><path d="M98 48l8 2-4 7z" fill="#1a74c8"/></svg>
<h2 class="abs agent-title">Find &nbsp;the right local<br><span class="underline">Agent for you</span></h2>
<p class="abs agent-note">Just some basic information. The address of your personal property will help in finding the right local agent for you.</p>
<p class="abs label" style="left:646px;top:2963px">Enter the address of your insurable property</p>
<div class="input" style="top:2994px"><svg width="16" height="12" viewBox="0 0 24 18"><rect width="24" height="18" rx="2" fill="#8fa8c8"/><path d="M2 2l10 8 10-8" stroke="#fff" stroke-width="2" fill="none"/></svg>Email address</div>
<p class="abs label" style="left:646px;top:3064px">Zip code (require)</p>
<div class="input" style="top:3088px"><svg width="12" height="15" viewBox="0 0 20 26"><path fill="#8fa8c8" d="M10 0a10 10 0 0 1 10 10c0 7-10 16-10 16S0 17 0 10A10 10 0 0 1 10 0z"/><circle cx="10" cy="10" r="3.5" fill="#fff"/></svg>Type Zip code</div>
<div class="btn btn-green" style="left:638px;top:3158px;width:174px;height:47px;font-size:14px">Next Step ›</div>

<!-- TESTIMONIALS -->
<div class="abs eyebrow" style="left:0;width:1200px;top:3332px;text-align:center;font-size:14px">Testimonials</div>
<h2 class="abs t-title">What Our Client Says <span class="underline">about us</span></h2>
<div class="abs t-side" style="left:190px;text-align:center">"As a CPA, I find this team especially like them. They help so much, and do find the savings I need for helpful clients."</div>
<div class="abs t-side" style="left:870px;text-align:center">"Easy to navigate. I got my policy doc or PDF. I hope very much to stay long."</div>
<div class="avatar" role="img" aria-label="Client portrait" style="left:236px;top:3440px;width:42px;height:42px"></div>
<div class="avatar" role="img" aria-label="Client portrait" style="left:200px;top:3683px;width:32px;height:32px"></div>
<div class="avatar" role="img" aria-label="Client portrait" style="left:990px;top:3432px;width:28px;height:28px;background:linear-gradient(135deg,#e8dcd2,#b9a596)"></div>
<div class="avatar" role="img" aria-label="Client portrait" style="left:1016px;top:3690px;width:40px;height:40px;background:linear-gradient(135deg,#e0d4c6,#a89484)"></div>
<div class="abs t-card">
  <svg style="margin-top:34px" width="48" height="34" viewBox="0 0 48 34"><path fill="#133f8c" d="M2 0h18v18l-8 16H4l6-14H2zM28 0h18v18l-8 16h-8l6-14h-8z"/></svg>
  <p style="margin:14px auto 0;width:480px;font-size:16.5px;line-height:22px;font-weight:600;color:#2b2f38">"Lorem ipsum dolor sit amet, consectetur adipiscing elit, sed do eiusmod tempor incididunt ut labore et dolore magna aliqua. Ut enim ad minim veniam, quis nostrud exercitation ullamco laboris n"</p>
  <p class="head" style="margin-top:18px;font-size:15px;font-weight:600;color:#133f8c">Dara Kellan</p>
  <p style="margin-top:4px;color:#f3b61f;font-size:18px;letter-spacing:2px">★★★★★</p>
</div>
<svg class="abs" style="left:132px;top:3564px" width="22" height="40" viewBox="0 0 22 40" aria-label="Previous"><path d="M20 2L3 20l17 18" stroke="#1a74c8" stroke-width="3" fill="none"/></svg>
<svg class="abs" style="left:1046px;top:3564px" width="22" height="40" viewBox="0 0 22 40" aria-label="Next"><path d="M2 2l17 18L2 38" stroke="#1a74c8" stroke-width="3" fill="none"/></svg>

<!-- CTA -->
<section class="abs cta">
  <span class="abs" style="left:82px;top:48px;width:44px;height:44px;border:3px solid #fff;border-radius:50%"></span>
  <h3 class="cta-title">Get Started with Brellow Cover Insurance</h3>
  <p class="cta-sub">Lorem ipsum dolor sit amet, consectetur adipiscin</p>
  <div class="cta-btn">Try For FREE →</div>
</section>

<!-- FOOTER -->
<footer>
  <div class="brand" style="left:151px;top:4018px">
    <span class="brand-dot" style="width:40px;height:40px"></span>
    <span class="brand-name" style="font-size:19px">Brellow Cover<br>Insurance, LP</span>
  </div>
  <p class="abs" style="left:155px;top:4086px;width:230px;font-size:11px;line-height:14px;color:#555b66">Lorem ipsum dolor sit amet, consectetur adipiscing elit, sed do eiusmod tempor incididunt ut labore et dolore</p>
  <div class="abs" style="left:160px;top:4154px;display:flex;gap:24px">
    <span class="social" aria-label="Social profile"></span><span class="social" aria-label="Social profile"></span><span class="social" aria-label="Social profile"></span>
  </div>
  <div class="abs f-col" style="left:435px;top:4021px">
    <h4>Navigation</h4>
    <ul><li>Home</li><li>About Us</li><li>Insurance</li><li>Services</li><li>Testimonials</li></ul>
  </div>
  <div class="abs f-col" style="left:654px;top:4019px">
    <h4>Insurance</h4>
    <ul><li>Auto Insurance</li><li>Home Insurance</li><li>Life Insurance</li><li>Car Insurance</li><li>Business Insurance</li></ul>
  </div>
  <div class="abs f-col" style="left:877px;top:4021px">
    <h4>Contact us</h4>
    <div class="f-contact"><svg width="14" height="14" viewBox="0 0 24 24"><path fill="#1a74c8" d="M6.6 10.8a15.1 15.1 0 0 0 6.6 6.6l2.2-2.2c.3-.3.7-.4 1-.2 1.1.4 2.3.6 3.6.6.6 0 1 .4 1 1V20c0 .6-.4 1-1 1A17 17 0 0 1 3 4c0-.6.4-1 1-1h3.5c.6 0 1 .4 1 1 0 1.3.2 2.5.6 3.6.1.3 0 .7-.2 1z"/></svg><span>Phone Number<br>(555) 218-0734</span></div>
    <div class="f-contact"><svg width="14" height="11" viewBox="0 0 24 18" style="margin-top:8px"><rect width="24" height="18" rx="2" fill="#1a74c8"/><path d="M2 2l10 8 10-8" stroke="#fff" stroke-width="2" fill="none"/></svg><span>Email address<br>info@brellowcover.com</span></div>
  </div>
  <div class="abs bottom">
    <span class="abs" style="left:160px;top:30px">© 2025 Brellow Cover Insurance, LP. All Rights Reserved</span>
    <span class="abs" style="left:903px;top:30px">Terms of use &nbsp; Privacy Policy &nbsp; Sitemap</span>
  </div>
</footer>

</body>
</html>
```